Harrowmere Freight, Project

Company Profile
Harrowmere Freight Sdn Bhd is a well established and experienced freight forwarder in Kuala Lumpur, Malaysia. We specialize in air and sea forwarding, Custom Brokerage and regulatory compliance services, inland transportation,
overseas freighting and warehousing and distribution management. With our dedicated qualified and experienced professionals, we are fully committed to serving our clients.

Our Mission
Based on the motto “Quick, Reliable and Polite”, Harrowmere Freight is dedicated to upholding the following three points corporate philosophy:
1. Adhering to the principle that “the customer always comes first”.
2. Contributing to the development of the local community.
3. Making it our duty to be responsible and sincere.

Our Edge
• One-Stop Logistics Solutions
• Extensive Network Throughout Malaysia
• Highly Qualified and Experienced Pool of Professionals
• Comprehensive IT Solutions
• Innovative and Customer-focused Solutions
• Flexible and Consistent in Managing Exceptions
• Total Supply Chain Visibility

Target Market(s)

We sell the logistics services to all the industry in Malaysia. (ONE Stop Logistics Solutions)

Industry/Entity Type

Logistic

Contact Information for Business Card

I want the back of the card to be white with the logo and slogan. i would like to see the logo on the front with the general info.

Requirements
Must have
• Name, Title, Office, Cell, Fax, Email, Address, Website
Nice to have
• Modern Design Business Card

```html
<!DOCTYPE html>
<html lang="en">
<head>
<meta charset="utf-8">
<title>Harrowmere Freight – Stationery</title>
<link href="https://fonts.googleapis.com/css2?family=Arimo:wght@400;700&family=Questrial&display=swap" rel="stylesheet">
<style>
:root{
  --bg:#e4e4e6;
  --paper:#ffffff;
  --blue:#1e9bd9;
  --blue-top:#24a9e1;
  --blue-deep:#1677c2;
  --ink:#2b2b2e;
  --muted:#5a5a5e;
  --soft:#eceef1;
}
*{margin:0;padding:0;box-sizing:border-box}
html,body{width:1189px;height:1200px;overflow:hidden;background:var(--bg)}
body{position:relative;font-family:"Arimo",Arial,sans-serif;color:var(--ink)}
.piece{position:absolute;background:var(--paper)}
.band{position:absolute;left:0;top:0;bottom:0;background:linear-gradient(180deg,var(--blue-top),var(--blue-deep))}
.brand{font-family:"Questrial",Arial,sans-serif;color:var(--blue);position:absolute;white-space:nowrap}
.brand .dot{display:inline-block;border-radius:50%;background:var(--blue);vertical-align:middle;margin-right:6px}
.tagline{font-family:"Questrial",Arial,sans-serif;color:var(--blue);position:absolute;letter-spacing:1.2px;white-space:nowrap}
.abs{position:absolute}

/* letterhead */
.letterhead{left:50px;top:110px;width:508px;height:657px}
.letterhead .band{width:34px}
.lh-company{right:39px;top:53px;text-align:right;font-family:"Questrial",Arial,sans-serif}
.lh-company h1{font-weight:400;font-size:13.4px;letter-spacing:.2px;color:var(--ink)}
.lh-company .reg{font-size:6.6px;color:var(--muted);margin-top:1px}
.lh-company .addr{font-size:8.2px;line-height:10.4px;color:var(--ink);margin-top:8px}
.lh-company .contact{font-size:8.2px;line-height:9.8px;margin-top:5px}
.lh-company .contact span{display:inline-block;width:6px;height:6px;background:var(--blue);margin-left:4px;vertical-align:-0.5px}
.recipient{left:75px;top:189px;font-size:8.4px;line-height:10.5px}
.recipient b{font-size:9.6px;display:block;margin-bottom:4px}
.letter-body{left:76px;top:261px;width:392px;font-size:8.9px;line-height:14.8px;color:#333}
.letter-body p+p{margin-top:14.8px}
.signoff{left:75px;top:514px;font-size:9px;line-height:11.5px}
.signature{left:75px;top:536px;width:120px;height:34px;background:linear-gradient(90deg,#e9ebef,#f5f6f8);border-radius:4px}
.signer{left:75px;top:576px;font-size:9.4px;line-height:11.6px}
.signer b{display:block}
.gst{right:39px;top:625px;font-size:7.2px;font-weight:700}

/* folder */
.folder{left:629px;top:111px;width:506px;height:654px;background:linear-gradient(180deg,var(--blue-top),var(--blue-deep))}
.folder .brand{color:#fff;left:0;right:0;text-align:center;top:358px;font-size:28px;letter-spacing:.5px}

/* envelope front */
.env-front{left:47px;top:849px;width:401px;height:201px}
.env-front .band{width:23px}
.env-front .title{right:16px;top:24px;text-align:right;font-size:5.9px;font-weight:700}
.env-front .title span{display:block;font-weight:400;color:var(--blue);font-size:4px;margin-top:1px}
.env-front .addr{left:37px;top:162px;font-size:4.6px;line-height:5.4px;color:var(--muted)}

/* envelope back */
.env-back{left:479px;top:849px;width:401px;height:201px;background:linear-gradient(180deg,var(--blue-top),var(--blue-deep))}
.env-back svg{position:absolute;left:0;top:0}
.env-back .brand{left:0;right:0;text-align:center;top:24px;font-size:9px}

/* business cards */
.card{width:215px;height:122px}
.card .band{width:21px}
.card-front{left:921px;top:805px}
.card-front .co{left:28px;top:43px;font-size:6.2px;font-weight:700}
.card-front .co span{display:block;font-weight:400;color:var(--blue);font-size:4px}
.card-front .person{left:28px;top:60px;font-size:6.4px;color:var(--blue);font-weight:700;white-space:nowrap}
.card-front .person em{font-style:normal;font-weight:400;color:var(--muted);font-size:5px;border-left:1px solid var(--muted);padding-left:3px;margin-left:2px}
.card-front .lines{left:28px;top:71px;font-size:5.1px;line-height:6.9px}
.card-front .lines i{display:inline-block;width:5px;height:5px;background:var(--blue-deep);margin-right:3px;vertical-align:-0.5px}
.card-front .addr{left:28px;top:101px;font-size:5px;line-height:6.2px;color:var(--muted)}
.card-front .brand{left:145px;top:41px;font-size:8.6px}
.card-front .tagline{left:145px;top:54px;font-size:3.6px;letter-spacing:.4px}
.card-back{left:921px;top:953px;height:123px}
.card-back h2{position:absolute;left:31px;top:13px;font-size:7px;color:var(--blue-deep);font-weight:700}
.card-back ul{position:absolute;left:31px;top:29px;list-style:none;font-size:5.3px;line-height:8.5px;color:var(--muted)}
.card-back li::before{content:"";display:inline-block;width:4px;height:4px;border-radius:50%;background:var(--blue);margin-right:5px;vertical-align:0}
.card-back .motto{left:31px;top:94px;font-size:6px;color:var(--blue);font-weight:700}
.card-back .web{left:31px;top:109px;font-size:5.1px;color:var(--muted)}
</style>
</head>
<body>

<!-- Letterhead -->
<section class="piece letterhead" aria-label="Letterhead">
  <div class="band"></div>
  <div class="brand" style="left:70px;top:110px;font-size:18px"><span class="dot" style="width:9px;height:9px"></span>Harrowmere Freight</div>
  <div class="tagline" style="left:86px;top:145px;font-size:7.4px">Quick, Reliable and Polite</div>

  <div class="abs lh-company">
    <h1>HARROWMERE FREIGHT SDN. BHD</h1>
    <div class="reg">(Company No. 1204876-K)</div>
    <div class="addr">No. 8B, 2nd Floor, Jalan Seri Mawar 3, Taman Seri Mawar<br>41050 Klang, Selangor Darul Ehsan, Malaysia.</div>
    <div class="contact">(603) 3372 5810<span></span><br>(603) 3372 5811<span></span><br>enquiry@harrowmere.com.my<span></span></div>
  </div>

  <div class="abs recipient"><b>AARON LIM</b>Street Name,City Name.<br>Zip Coad 0000</div>

  <div class="abs letter-body">
    <p>Lorem Ipsum is simply dummy text of the printing and typesetting industry. Lorem Ipsum has the been the industry's standard dummy text ever since the 1500s, when an unknown printer took a galley of type and scrambled it to make a type specimen book. It has survived not only five centuries, but also the leap into electronic typesetting, remaining essentially unchanged. It was popularised in the 1960s with the release of Letraset sheets containing Lorem Ipsum passages, and more recently with desktop publishing software like Aldus PageMaker including versions of the Lorem Ipsum.</p>
    <p>It is a long established fact that a reader will be distracted by the readable content of a page when looking at its layout. The point of using Lorem Ipsum is that it has a more-or-less normal distribution of letters, as opposed to using 'Content here, content here', making it look like readable English. Many desktop publishing packages and web page editors now use Lorem Ipsum as their default model text, and a search for 'lorem ipsum' will uncover many web sites still in their infancy. Various versions have evolved over the years, sometimes by accident, sometimes on purpose (injected humour and the like).</p>
  </div>

  <div class="abs signoff">Regards,</div>
  <div class="abs signature" role="img" aria-label="Handwritten signature of Daniel Tan"></div>
  <div class="abs signer"><b>Daniel Tan</b>General Maneger</div>
  <div class="abs gst">GST Registration No: 000418520917</div>
</section>

<!-- Presentation folder -->
<section class="piece folder" aria-label="Presentation folder">
  <div class="brand">Harrowmere Freight</div>
</section>

<!-- Envelope front -->
<section class="piece env-front" aria-label="Envelope front">
  <div class="band"></div>
  <div class="brand" style="left:37px;top:52px;font-size:11.5px">Harrowmere Freight</div>
  <div class="tagline" style="left:38px;top:71px;font-size:4.6px;letter-spacing:.6px">Quick, Reliable and Polite</div>
  <div class="abs title">HARROWMERE FREIGHT SDN. BHD.<span>(1204876-K)</span></div>
  <div class="abs addr">No. 8B, 2nd Floor,<br>Jalan Seri Mawar 3,<br>Taman Seri Mawar, 41050 Klang,<br>Selangor Darul Ehsan, Malaysia.</div>
</section>

<!-- Envelope back -->
<section class="piece env-back" aria-label="Envelope back">
  <svg width="401" height="60" viewBox="0 0 401 60" aria-hidden="true">
    <path d="M0 0 H401 L392 50 Q390 57 382 57 H19 Q11 57 9 50 Z" fill="#ffffff"/>
  </svg>
  <div class="brand">Harrowmere Freight</div>
</section>

<!-- Business card front -->
<section class="piece card card-front" aria-label="Business card front">
  <div class="band"></div>
  <div class="abs co">HARROWMERE FREIGHT SDN. BHD.<span>(1204876-K)</span></div>
  <div class="abs person">Faizal Rahman<em>Managing Director</em></div>
  <div class="abs lines">
    <div><i></i>+6012-470 2281</div>
    <div><i></i>(603) 3372 5808 / 5810</div>
    <div><i></i>(603) 3372 5811</div>
    <div><i></i>faizal.rahman@harrowmere.com.my</div>
  </div>
  <div class="abs addr">No. 8B, 2nd Floor, Jalan Seri Mawar 3, Taman Seri Mawar,<br>41050 Klang, Selangor Darul Ehsan, Malaysia.</div>
  <div class="brand" style="font-size:7.4px">Harrowmere<br>Freight</div>
  <div class="tagline" style="top:66px">Quick, Reliable and Polite</div>
</section>

<!-- Business card back -->
<section class="piece card card-back" aria-label="Business card back">
  <div class="band"></div>
  <h2>We're Specialize In</h2>
  <ul>
    <li>One-Stop Logistics Solutions</li>
    <li>Extensive Network Throughout Malaysia</li>
    <li>Highly Qualified and Experienced Pool of Professionals</li>
    <li>Comprehensive IT Solutions</li>
    <li>Innovative and Customer-focused Solutions</li>
    <li>Flexible and Consistent in Managing Exceptions</li>
    <li>Total Supply Chain Visibility</li>
  </ul>
  <div class="abs motto">ONE STOP LOGISTICS SOLUTIONS</div>
  <div class="abs web">www.harrowmere.com.my</div>
</section>

</body>
</html>
```